BOLD & MINIMALIST DESIGN NEEDED

We want a very bold but minimalistic business card design that is impactful and utilizes both sides of the business card. Our current logo is included for your use.

We want bold fonts and good use of negative space. We don't want the logo to overpower the design.

Target Market(s)

Professionals who are building new commercial buildings.

Industry/Entity Type

Construction

Contact Information for Business Card

Name, Title, email, office phone, cell phone, website

Font styles to use
Serif
Sans Serif

Requirements
Must have
• Bold design!

```html
<!DOCTYPE html>
<html lang="en">
<head>
<meta charset="utf-8">
<title>Ridgeline Design + Build — Business Card</title>
<link href="https://fonts.googleapis.com/css2?family=Roboto:wght@300;400;700&display=swap" rel="stylesheet">
<style>
  :root {
    --backdrop: #dcdcdc;
    --card-black: #0b0c0e;
    --card-white: #ffffff;
    --accent-green: #7dc242;
    --text-light: #f2f2f2;
    --text-dark: #111111;
    --rule-grey: #8a8a8a;
  }
  html, body {
    margin: 0;
    padding: 0;
    width: 1200px;
    height: 1200px;
    overflow: hidden;
    background: var(--backdrop);
    font-family: "Roboto", sans-serif;
  }
  .canvas {
    position: relative;
    width: 1200px;
    height: 1200px;
  }
  .card {
    position: absolute;
    width: 686px;
    height: 392px;
    overflow: hidden;
  }
  .card-front {
    left: 261px;
    top: 165px;
    background: var(--card-black);
    display: flex;
    align-items: center;
    justify-content: center;
  }
  .card-back {
    left: 262px;
    top: 653px;
    display: flex;
  }
  .back-info {
    position: relative;
    width: 343px;
    height: 100%;
    background: var(--card-black);
    color: var(--text-light);
    font-weight: 300;
  }
  .back-brand {
    width: 343px;
    height: 100%;
    background: var(--card-white);
    display: flex;
    align-items: center;
    justify-content: center;
  }
  .wordmark {
    display: flex;
    align-items: center;
    gap: 12px;
    font-weight: 700;
    letter-spacing: 1px;
    white-space: nowrap;
  }
  .wordmark-square {
    width: 20px;
    height: 20px;
    background: var(--accent-green);
  }
  .card-front .wordmark {
    color: var(--text-light);
    font-size: 34px;
  }
  .card-front .wordmark-square {
    width: 28px;
    height: 28px;
  }
  .back-brand .wordmark {
    color: var(--text-dark);
    font-size: 22px;
  }
  .person-name {
    position: absolute;
    left: 45px;
    top: 92px;
    margin: 0;
    font-size: 24px;
    font-weight: 300;
    color: var(--accent-green);
    letter-spacing: 0.3px;
  }
  .name-rule {
    position: absolute;
    left: 0;
    top: 124px;
    width: 243px;
    height: 1px;
    background: var(--rule-grey);
  }
  .person-title {
    position: absolute;
    left: 45px;
    top: 130px;
    margin: 0;
    font-size: 16px;
    font-weight: 400;
    letter-spacing: 0.5px;
  }
  .address {
    position: absolute;
    left: 45px;
    top: 192px;
    margin: 0;
    font-style: normal;
    font-size: 15.5px;
    line-height: 19px;
  }
  .contact-list {
    position: absolute;
    left: 45px;
    top: 245px;
    margin: 0;
    padding: 0;
    list-style: none;
    font-size: 15.5px;
    line-height: 19.5px;
  }
  .contact-list li {
    display: flex;
    align-items: center;
    gap: 10px;
  }
  .contact-icon {
    width: 13px;
    height: 13px;
    fill: var(--accent-green);
    flex: none;
  }
</style>
</head>
<body>
<main class="canvas">

  <section class="card card-front" aria-label="Card front">
    <div class="wordmark">
      <span class="wordmark-square"></span>
      <span>RIDGELINE DESIGN + BUILD</span>
    </div>
  </section>

  <section class="card card-back" aria-label="Card back">
    <div class="back-info">
      <h1 class="person-name">Daniel Brooks</h1>
      <div class="name-rule"></div>
      <p class="person-title">President</p>
      <address class="address">4120 Alder Street<br>Juneau, Alaska 99801</address>
      <ul class="contact-list">
        <li>
          <svg class="contact-icon" viewBox="0 0 16 16" aria-hidden="true">
            <path d="M3.6 1l2.3 3.2-1.4 1.6c.9 2 2.6 3.7 4.6 4.6l1.6-1.4L14 11.3l-.8 2.8c-.2.5-.7.9-1.3.8C6.2 14.4 1.6 9.8 1.1 4.1 1 3.5 1.4 3 1.9 2.8z"/>
          </svg>
          <span>555-014-2278</span>
        </li>
        <li>
          <svg class="contact-icon" viewBox="0 0 16 16" aria-hidden="true">
            <path d="M1 3h14v1.2L8 8.6 1 4.2zM1 5.6l7 4.4 7-4.4V13H1z"/>
          </svg>
          <span>info@ridgelinebuild.com</span>
        </li>
        <li>
          <svg class="contact-icon" viewBox="0 0 16 16" aria-hidden="true">
            <circle cx="8" cy="8" r="7"/>
            <path d="M4 5.5c1.5-.5 2.5.5 2 1.8s1 2 .5 3.2M10 3.5c-.5 1.5.8 2 1.8 2.5M9.5 12c.3-1.3 1.5-1.5 2.5-1" stroke="#0b0c0e" stroke-width="1.2" fill="none"/>
          </svg>
          <span>www.ridgelinebuild.com</span>
        </li>
      </ul>
    </div>
    <div class="back-brand">
      <div class="wordmark">
        <span class="wordmark-square"></span>
        <span>RIDGELINE DESIGN + BUILD</span>
      </div>
    </div>
  </section>

</main>
</body>
</html>
```